Association qui souhaite améliorer l'accès aux personnes en situation de handicap

Nous sommes une association qui a pour objectif d'améliorer l'accessibilité, augmenter l'offre des activités réalisables dans notre région touristique.
Nous souhaitons réaliser un site internet afin de pouvoir communiquer sur notre association. Nous avons déjà conçu notre flyer sur Plumotrix. Nous souhaiterions une base graphique se rapportant à celui-ci. C'est possible de tout retravailler mais nous souhaitons tout de même retrouver la charte graphique ou code couleur du flyer.
Il nous faudrait quelques pages:
- 1 page : Acceuil / Présentation (Home), Il y aurait le descriptif de l'association, avec ses objectifs à +/- moyen terme
- 1 page : Nos réalisations, celle-ci présenterait les éléments que nous avons réalisés avec des zones de textes et des images classées chronologiquement au fur et à mesure des nouveautés
- 1 page : Media, comme la précédente, mais ou on pourrait voir ou lire sur les divers médias qui parlent de nous
- 1 page : Evenements : c'est une page pour présenter divers activités que nous allons organiser
- 1 page : Contact qui indique comment nous contacter et avec la présentation des 5 ou 6 membres du comité
- 1 link donate : qui arrive sur un formulaire de donnée que l'on pourra faire évoluer sur un système de payement par la suite. Cette bannière doit se retrouver sur toutes les pages
Il est nécessaire que se design puisse être transféré sur une lecture sur téléphone mobile
Personnes en situation de handicap
Associatif

```html
<!DOCTYPE html>
<html lang="en">
<head>
<meta charset="utf-8">
<title>OpenPath Association</title>
<link href="https://fonts.googleapis.com/css2?family=Oswald:wght@500;600&family=Outfit:wght@400;500&display=swap" rel="stylesheet">
<style>
:root{
  --red:#c8202f;
  --red-dark:#a51824;
  --ink:#222428;
  --dark:#2a3035;
  --dark-2:#353c42;
  --muted:#5b6066;
  --light:#f3f4f6;
  --line:#e2e4e7;
  --white:#ffffff;
}
*{box-sizing:border-box;margin:0;padding:0}
html,body{width:1200px;height:4839px;overflow:hidden}
body{font-family:"Outfit",sans-serif;color:var(--ink);background:var(--white);position:relative}
.head{font-family:"Oswald",sans-serif;font-weight:600;text-transform:uppercase;letter-spacing:.5px}
.abs{position:absolute}
.arr{width:14px;height:12px;fill:none;stroke:currentColor;stroke-width:1.8;stroke-linecap:round;stroke-linejoin:round;vertical-align:middle}
.btn{display:inline-flex;align-items:center;justify-content:center;gap:14px;font-family:"Oswald",sans-serif;font-weight:500;text-transform:uppercase;font-size:16px;letter-spacing:.4px}
.btn-red{background:var(--red);color:var(--white)}
.btn-outline-red{border:2px solid var(--red);color:var(--red);background:var(--white)}
.btn-outline-white{border:2px solid var(--white);color:var(--white)}
.btn-dark{background:var(--ink);color:var(--white)}
.brand{display:flex;align-items:center;gap:12px}
.brand-mark{width:30px;height:30px;background:var(--red)}
.brand-name{font-family:"Oswald",sans-serif;font-weight:600;font-size:22px;line-height:1.05;color:var(--ink);text-transform:uppercase}
.section-icon{width:50px;height:30px;border-bottom:4px solid var(--red)}
.section-title{font-size:46px;line-height:1.1}
/* header */
.site-header{position:absolute;top:0;left:0;width:1200px;height:126px;background:var(--white);z-index:5}
.top-line{position:absolute;top:0;left:0;width:1200px;height:4px;background:var(--red)}
.top-band{position:absolute;top:0;right:0;width:570px;height:42px;background:var(--red);clip-path:polygon(20px 0,100% 0,100% 100%,0 100%);color:var(--white);font-size:15px;display:flex;align-items:center;padding-left:58px;gap:0}
.top-band b{font-weight:500}
.top-band .sep{margin:0 10px;opacity:.7}
.top-band .stay{margin-left:auto;margin-right:12px}
.top-band .dot{width:11px;height:11px;border-radius:50%;background:var(--white);margin-right:14px}
.nav{position:absolute;top:76px;left:582px;display:flex;gap:33px;font-size:14px;font-weight:500;text-transform:uppercase}
.nav a{color:var(--ink);text-decoration:none;position:relative}
.nav a.active::before{content:"";position:absolute;top:-20px;left:50%;margin-left:-10px;width:20px;height:12px;border-bottom:3px solid var(--red)}
/* hero */
.hero{position:absolute;top:126px;left:0;width:1200px;height:729px}
.hero svg{position:absolute;inset:0}
.hero-copy{position:absolute;left:682px;top:60px;color:var(--white);width:440px}
.hero-copy .mini{width:46px;height:26px;border-bottom:4px solid var(--red);margin-bottom:14px}
.hero-copy h1{font-size:58px;line-height:1.08;font-weight:600}
.hero-copy p{font-size:17px;line-height:31px;margin-top:18px}
.hero-copy .btn{margin-top:26px;width:229px;height:53px}
.slide-arrow{position:absolute;width:34px;height:90px;background:rgba(30,34,38,.8);color:var(--white);display:flex;align-items:center;justify-content:center}
/* welcome */
.welcome{position:absolute;top:855px;left:0;width:1200px;height:605px}
.cross-badge{position:absolute;left:92px;top:84px;width:42px;height:42px;background:var(--red)}
.cross-badge::before,.cross-badge::after{content:"";position:absolute;background:var(--white)}
.cross-badge::before{left:17px;top:8px;width:8px;height:26px}
.cross-badge::after{left:8px;top:17px;width:26px;height:8px}
.welcome h2{position:absolute;left:92px;top:134px;font-size:46px;line-height:52px;color:var(--ink)}
.welcome h2 span{color:var(--red)}
.welcome p{position:absolute;left:92px;top:262px;width:520px;font-size:18px;line-height:30px}
.welcome-photo{position:absolute;left:682px;top:3px;width:426px;height:513px}
/* achievements */
.achievements{position:absolute;top:1460px;left:0;width:1200px;height:863px;background:linear-gradient(120deg,#262b30,#3a4147 55%,#2a3035);color:var(--white);text-align:center}
.center-head{position:absolute;left:0;width:1200px;text-align:center}
.center-head .section-icon{margin:0 auto}
.center-head p{font-size:18px;line-height:30px;margin-top:14px}
.ach-card{position:absolute;top:324px;width:323px;height:338px}
.ach-card .ph{position:absolute;inset:0}
.ach-label{position:absolute;left:22px;bottom:0;right:0;height:45px;background:var(--white);color:var(--ink);clip-path:polygon(20px 0,100% 0,100% 100%,0 100%);display:flex;align-items:center;justify-content:center;font-size:19px}
.ach-card.active .ach-label{background:var(--red);color:var(--white)}
.ach-go{position:absolute;right:0;bottom:45px;width:50px;height:50px;background:var(--red);color:var(--white);display:flex;align-items:center;justify-content:center}
.ach-card.active .ach-go{background:var(--white);color:var(--red)}
.side-arrow{position:absolute;color:var(--white)}
.side-arrow svg{width:48px;height:22px;fill:none;stroke:currentColor;stroke-width:2}
/* media */
.media{position:absolute;top:2323px;left:0;width:1200px;height:945px}
.media .section-icon{position:absolute;left:92px;top:79px}
.media h2{position:absolute;left:92px;top:137px;color:var(--ink)}
.media h2 span{color:var(--red)}
.media .lead{position:absolute;left:92px;top:212px;width:520px;font-size:18px;line-height:30px}
.media .view-more{position:absolute;left:926px;top:147px;width:180px;height:54px}
.media-card{position:absolute;width:498px;height:257px;border:1px solid var(--line);border-radius:6px;box-shadow:0 4px 14px rgba(0,0,0,.06);background:var(--white)}
.media-card .ph{position:absolute;left:11px;top:12px;width:165px;height:232px}
.media-card .body{position:absolute;left:198px;top:28px;width:280px}
.media-card h3{font-size:18px;line-height:28px;color:var(--ink)}
.media-card p{font-size:16px;line-height:30px;margin-top:10px}
.media-card .btn{margin-top:14px;width:172px;height:42px;font-size:15px}
/* events */
.events{position:absolute;top:3268px;left:0;width:1200px;height:1112px;color:var(--white)}
.events svg.bg{position:absolute;inset:0}
.ev-card{position:absolute;top:479px;width:323px;height:473px;background:var(--white);color:var(--ink)}
.ev-card .ph{position:absolute;left:0;top:0;width:323px;height:225px}
.ev-date{position:absolute;right:16px;top:0;width:56px;height:80px;background:var(--red);color:var(--white);text-align:center;padding-top:10px}
.ev-date b{display:block;font-family:"Oswald",sans-serif;font-weight:500;font-size:28px;line-height:32px}
.ev-date span{display:block;margin:4px auto 0;width:44px;background:var(--white);color:var(--ink);font-size:13px;font-weight:500;text-transform:uppercase;line-height:20px}
.ev-body{position:absolute;left:25px;top:249px;width:280px}
.ev-by{font-size:14px;color:var(--muted)}
.ev-body h3{font-size:18px;line-height:28px;margin-top:8px}
.ev-body p{font-size:16px;line-height:30px;margin-top:12px}
.ev-more{display:flex;align-items:center;gap:16px;margin-top:22px;font-family:"Oswald",sans-serif;font-weight:500;color:var(--red);font-size:16px;text-transform:uppercase}
/* donate */
.donate{position:absolute;top:4314px;left:94px;width:1014px;height:128px;background:linear-gradient(90deg,var(--red-dark),var(--red) 40%,var(--red));clip-path:polygon(0 0,96% 0,100% 100%,4% 100%);color:var(--white);z-index:3}
.donate h2{position:absolute;left:90px;top:26px;font-size:30px;line-height:38px}
.donate .divider{position:absolute;left:571px;top:20px;width:2px;height:88px;background:rgba(255,255,255,.8)}
.donate .btn{position:absolute;left:702px;top:43px;width:218px;height:55px}
/* footer */
.site-footer{position:absolute;top:4442px;left:0;width:1200px;height:397px;background:var(--light)}
.site-footer .brand{position:absolute;left:92px;top:112px}
.socials{position:absolute;left:92px;top:215px;display:flex;gap:12px}
.socials span{width:44px;height:44px;border:2px solid var(--ink);border-radius:6px;display:flex;align-items:center;justify-content:center}
.socials span::after{content:"";width:10px;height:10px;border-radius:50%;background:var(--ink)}
.f-col{position:absolute;top:92px}
.f-col h4{font-size:22px;color:var(--ink);margin-bottom:18px}
.f-col li{list-style:none;font-size:16px;line-height:33px}
.contact-row{display:flex;gap:17px;margin-bottom:22px;font-size:16px;line-height:28px}
.contact-row i{flex:0 0 41px;height:41px;border-radius:50%;background:var(--red);display:flex;align-items:center;justify-content:center}
.contact-row i svg{width:18px;height:18px;fill:none;stroke:var(--white);stroke-width:1.8}
.f-bottom{position:absolute;left:92px;top:339px;width:1016px;border-top:1px solid var(--line);text-align:center;padding-top:18px;font-size:14px;color:var(--muted)}
</style>
</head>
<body>

<header class="site-header">
  <div class="top-line"></div>
  <div class="top-band">
    <svg width="18" height="18" viewBox="0 0 24 24" fill="none" stroke="#fff" stroke-width="1.8"><path d="M5 3h4l2 5-2.5 1.5a11 11 0 0 0 6 6L16 13l5 2v4a2 2 0 0 1-2 2A16 16 0 0 1 3 5a2 2 0 0 1 2-2z"/></svg>
    <span class="sep">|</span>Call Us:&nbsp;<b>123-555-0147</b>
    <span class="stay">Stay with us:</span>
    <span class="dot"></span><span class="dot"></span><span class="dot"></span>
  </div>
  <div class="brand abs" style="left:92px;top:32px">
    <span class="brand-mark"></span>
    <span class="brand-name">OpenPath<br>Association</span>
  </div>
  <nav class="nav">
    <a class="active" href="#">Home</a>
    <a href="#">Our Achievements</a>
    <a href="#">Media</a>
    <a href="#">Events</a>
    <a href="#">Contact</a>
  </nav>
</header>

<section class="hero">
  <svg width="1200" height="729" viewBox="0 0 1200 729">
    <defs>
      <linearGradient id="heroGrad" x1="0" y1="0" x2="1" y2="1">
        <stop offset="0" stop-color="#4c5a45"/>
        <stop offset=".45" stop-color="#6f7468"/>
        <stop offset="1" stop-color="#3d4440"/>
      </linearGradient>
    </defs>
    <polygon role="img" aria-label="Photo of a helper guiding a person in a wheelchair down outdoor steps" points="0,0 1200,0 1200,434 0,667" fill="url(#heroGrad)"/>
    <polygon points="0,334 330,603 0,729" fill="#c8202f"/>
  </svg>
  <div class="slide-arrow" style="left:0;top:152px"><svg class="arr" viewBox="0 0 14 12" style="transform:scaleX(-1)"><path d="M1 6h11M7 1l5 5-5 5"/></svg></div>
  <div class="slide-arrow" style="right:0;top:152px"><svg class="arr" viewBox="0 0 14 12"><path d="M1 6h11M7 1l5 5-5 5"/></svg></div>
  <div class="hero-copy">
    <div class="mini"></div>
    <h1 class="head">Rejoin the<br>Association</h1>
    <p>Friends living in the region who are committed to making the Haut-Val region as accessible as possible to people with disabilities.</p>
    <a class="btn btn-red">Contact Us Now <svg class="arr" viewBox="0 0 14 12"><path d="M1 6h11M7 1l5 5-5 5"/></svg></a>
  </div>
</section>

<section class="welcome">
  <div class="cross-badge"></div>
  <h2 class="head">Welcome to<br>OpenPath <span>Association</span></h2>
  <p>Lorem ipsum dolor sit ameti consectetur adipisicing elit sed do eiusmod tempor incididunt ut labore et doloreu magna aliqua. Ut enim ad minim veniam, quis nostrud exercitation ullamco laboris nisi ut aliquip ex ea comon consequat. Duis aute irure dolor in reprehenderit. Ut ito enim ad minim veniam, quis nostrud exercitation.</p>
  <svg class="welcome-photo" viewBox="0 0 426 513">
    <polygon role="img" aria-label="Photo of a carer helping a woman on crutches rise from a sofa" points="0,0 426,0 426,360 0,470" fill="#9aa3a8"/>
    <polygon points="0,270 320,440 0,513" fill="#c8202f"/>
  </svg>
</section>

<section class="achievements">
  <div class="center-head" style="top:92px">
    <div class="section-icon"></div>
    <h2 class="head section-title" style="margin-top:20px">Our Achievements</h2>
    <p>Lorem ipsum dolor sit ameti consectetur adipisicing elit<br>sed do eiusmod tempor incididunt ut labore et</p>
  </div>
  <div class="side-arrow" style="left:22px;top:482px"><svg viewBox="0 0 48 22"><path d="M47 11H2M12 1 2 11l10 10"/></svg></div>
  <div class="side-arrow" style="right:22px;top:482px"><svg viewBox="0 0 48 22"><path d="M1 11h45M36 1l10 10-10 10"/></svg></div>

  <article class="ach-card" style="left:92px">
    <div class="ph" role="img" aria-label="Photo of a smiling man in sunglasses and a cap outdoors" style="background:linear-gradient(160deg,#6d8a45,#d8704f)"></div>
    <a class="ach-go"><svg class="arr" viewBox="0 0 14 12"><path d="M1 6h11M7 1l5 5-5 5"/></svg></a>
    <div class="ach-label head">Lorem ipsum dolar sit</div>
  </article>
  <article class="ach-card active" style="left:439px">
    <div class="ph" role="img" aria-label="Photo of a smiling boy in a classroom" style="background:linear-gradient(160deg,#b59a6a,#7d96b0)"></div>
    <a class="ach-go"><svg class="arr" viewBox="0 0 14 12"><path d="M1 6h11M7 1l5 5-5 5"/></svg></a>
    <div class="ach-label head">Lorem ipsum dolar sit</div>
  </article>
  <article class="ach-card" style="left:785px">
    <div class="ph" role="img" aria-label="Photo of a smiling older woman in a wheelchair" style="background:linear-gradient(160deg,#8e9799,#b9c6d2)"></div>
    <a class="ach-go"><svg class="arr" viewBox="0 0 14 12"><path d="M1 6h11M7 1l5 5-5 5"/></svg></a>
    <div class="ach-label head">Lorem ipsum dolar sit</div>
  </article>

  <a class="btn btn-outline-white abs" style="left:458px;top:722px;width:284px;height:54px">View All Achievements <svg class="arr" viewBox="0 0 14 12"><path d="M1 6h11M7 1l5 5-5 5"/></svg></a>
</section>

<section class="media">
  <div class="section-icon"></div>
  <h2 class="head section-title">Our <span>Media</span></h2>
  <p class="lead">Lorem ipsum dolor sit ameti consectetur adipisicing elit sed do eiusmod tempor incididunt ut labore et</p>
  <a class="btn btn-red view-more">View More <svg class="arr" viewBox="0 0 14 12"><path d="M1 6h11M7 1l5 5-5 5"/></svg></a>

  <article class="media-card" style="left:92px;top:321px">
    <div class="ph" role="img" aria-label="Photo of a woman with a white cane walking in a park" style="background:linear-gradient(160deg,#5d6a45,#c88a4a)"></div>
    <div class="body"><h3 class="head">Sed ut perspiciatis under a omnis iste natus error to</h3><p>Lorem ipsum dolor sit ameti top sed consectetur adipisicing elit</p><a class="btn btn-outline-red">View More <svg class="arr" viewBox="0 0 14 12"><path d="M1 6h11M7 1l5 5-5 5"/></svg></a></div>
  </article>
  <article class="media-card" style="left:608px;top:321px">
    <div class="ph" role="img" aria-label="Photo of a young girl smiling" style="background:linear-gradient(160deg,#c9b8a0,#e6ddd8)"></div>
    <div class="body"><h3 class="head">Sed ut perspiciatis under a omnis iste natus error to</h3><p>Lorem ipsum dolor sit ameti top sed consectetur adipisicing elit</p><a class="btn btn-outline-red">View More <svg class="arr" viewBox="0 0 14 12"><path d="M1 6h11M7 1l5 5-5 5"/></svg></a></div>
  </article>
  <article class="media-card" style="left:92px;top:595px">
    <div class="ph" role="img" aria-label="Photo of two hands holding each other" style="background:linear-gradient(160deg,#a8b4c0,#c8936f)"></div>
    <div class="body"><h3 class="head">Sed ut perspiciatis under a omnis iste natus error to</h3><p>Lorem ipsum dolor sit ameti top sed consectetur adipisicing elit</p><a class="btn btn-outline-red">View More <svg class="arr" viewBox="0 0 14 12"><path d="M1 6h11M7 1l5 5-5 5"/></svg></a></div>
  </article>
  <article class="media-card" style="left:608px;top:595px">
    <div class="ph" role="img" aria-label="Photo of an older woman with glasses and a walker" style="background:linear-gradient(160deg,#9ea8a6,#5d6873)"></div>
    <div class="body"><h3 class="head">Sed ut perspiciatis under a omnis iste natus error to</h3><p>Lorem ipsum dolor sit ameti top sed consectetur adipisicing elit</p><a class="btn btn-outline-red">View More <svg class="arr" viewBox="0 0 14 12"><path d="M1 6h11M7 1l5 5-5 5"/></svg></a></div>
  </article>
</section>

<section class="events">
  <svg class="bg" width="1200" height="1112" viewBox="0 0 1200 1112">
    <defs>
      <linearGradient id="evGrad" x1="0" y1="0" x2="1" y2="1">
        <stop offset="0" stop-color="#353b41"/>
        <stop offset=".5" stop-color="#2b3136"/>
        <stop offset="1" stop-color="#24292d"/>
      </linearGradient>
    </defs>
    <polygon role="img" aria-label="Dimmed photo of a man with sunglasses and a woman with glasses" points="0,310 860,122 1200,60 1200,1112 0,1112" fill="url(#evGrad)"/>
    <polygon points="860,122 1200,48 1200,62 880,132" fill="#ffffff"/>
    <polygon points="1200,0 875,122 1200,396" fill="#c8202f"/>
  </svg>
  <div class="center-head" style="top:262px">
    <div class="section-icon"></div>
    <h2 class="head section-title" style="margin-top:18px">Latest Events</h2>
    <p>Lorem ipsum dolor sit ameti consectetur adipisicing elit<br>sed do eiusmod tempor incididunt ut labore et</p>
  </div>
  <div class="side-arrow" style="left:18px;top:604px"><svg viewBox="0 0 48 22"><path d="M47 11H2M12 1 2 11l10 10"/></svg></div>
  <div class="side-arrow" style="right:18px;top:604px"><svg viewBox="0 0 48 22"><path d="M1 11h45M36 1l10 10-10 10"/></svg></div>

  <article class="ev-card" style="left:92px">
    <div class="ph" role="img" aria-label="Photo of a woman in a wheelchair on a train platform" style="background:linear-gradient(160deg,#9aa6b4,#d6d9dd)"></div>
    <div class="ev-date"><b>24</b><span>Mar</span></div>
    <div class="ev-body"><div class="ev-by">Event By Marion Keller</div><h3 class="head">Sed ut perspiciatis under a omnis iste natus error to</h3><p>Lorem ipsum dolor sit ameti top sed consectetur adipisicing elit</p><a class="ev-more">View More <svg class="arr" viewBox="0 0 14 12"><path d="M1 6h11M7 1l5 5-5 5"/></svg></a></div>
  </article>
  <article class="ev-card" style="left:439px">
    <div class="ph" role="img" aria-label="Photo of a man with a white cane walking in a green park" style="background:linear-gradient(160deg,#7e9a5e,#cfd8b8)"></div>
    <div class="ev-date"><b>03</b><span>May</span></div>
    <div class="ev-body"><div class="ev-by">Event By Marion Keller</div><h3 class="head">Sed ut perspiciatis under a omnis iste natus error to</h3><p>Lorem ipsum dolor sit ameti top sed consectetur adipisicing elit</p><a class="ev-more">View More <svg class="arr" viewBox="0 0 14 12"><path d="M1 6h11M7 1l5 5-5 5"/></svg></a></div>
  </article>
  <article class="ev-card" style="left:785px">
    <div class="ph" role="img" aria-label="Photo of a smiling boy seated by a window" style="background:linear-gradient(160deg,#4a3a2e,#a07a52)"></div>
    <div class="ev-date"><b>12</b><span>Jun</span></div>
    <div class="ev-body"><div class="ev-by">Event By Marion Keller</div><h3 class="head">Sed ut perspiciatis under a omnis iste natus error to</h3><p>Lorem ipsum dolor sit ameti top sed consectetur adipisicing elit</p><a class="ev-more">View More <svg class="arr" viewBox="0 0 14 12"><path d="M1 6h11M7 1l5 5-5 5"/></svg></a></div>
  </article>
</section>

<aside class="donate">
  <h2 class="head">Need help to<br>improve accessibility</h2>
  <span class="divider"></span>
  <a class="btn btn-dark">Donate Us Now <svg class="arr" viewBox="0 0 14 12"><path d="M1 6h11M7 1l5 5-5 5"/></svg></a>
</aside>

<footer class="site-footer">
  <div class="brand">
    <span class="brand-mark"></span>
    <span class="brand-name">OpenPath<br>Association</span>
  </div>
  <div class="socials"><span></span><span></span><span></span></div>
  <div class="f-col" style="left:441px">
    <h4 class="head">Quick Links</h4>
    <ul><li>Home</li><li>Our Achievements</li><li>Media</li><li>Events</li></ul>
  </div>
  <div class="f-col" style="left:672px">
    <h4 class="head">Other Links</h4>
    <ul><li>Privacy Policy</li><li>Terms &amp; Condition</li><li>FAQ</li><li>Contact</li></ul>
  </div>
  <div class="f-col" style="left:900px">
    <h4 class="head">Contact Info</h4>
    <div class="contact-row"><i><svg viewBox="0 0 24 24"><path d="M12 22s7-7 7-12a7 7 0 0 0-14 0c0 5 7 12 7 12z"/><circle cx="12" cy="10" r="2.5"/></svg></i><span>Rue des Cimes 8<br>1900 Montclair</span></div>
    <div class="contact-row"><i><svg viewBox="0 0 24 24"><path d="M5 3h4l2 5-2.5 1.5a11 11 0 0 0 6 6L16 13l5 2v4a2 2 0 0 1-2 2A16 16 0 0 1 3 5a2 2 0 0 1 2-2z"/></svg></i><span>Phone:<br>123-555-0147</span></div>
  </div>
  <div class="f-bottom">Copyright © 2022 OpenPath Association. All rights reserved.</div>
</footer>

</body>
</html>
```